verdant terraces simple classy business card design

my name is colin barrow and I run a gardening business aimed at high class verdant terraces. the business name is verdant terraces and our logo was designed on pixel harbour .My clientel are anything from residential homes to businesses. I take pride in my work and know that I offer a service like no other in my area.
The business card will be used to represent my business and I want it to be not only rememberable, but simplistic and modern. Eye catching too. Of course I would like it relatable to gardening and appealing to the correct clientel - those being garden enthusiasts, prestigious homes and businesses that are after top of the line gardening services like no other on the market.
I am not a typical lawn mowing business so I don't want a typical card design that represents that. The gardens I work with are generally million dollar properties with owners who are very garden proud looking for upkeep and guidance from me along with sometimes whole new garden designs. I want the business cards to show to my clients that I take pride, as they do, in their garden. And I want them to know from my card that I am a professional, qualified horticulturist offering them a top of the line service for life. I want them to refer my business on. I want them to look at my business card and see class and professionalism in a modern unique bold way.
The card should be simple with the possibility of the logo on the front being embossed/debossed and my details on the back the card should have a organic garden feel it's very important to me that it is absolutely perfect
I am also very open to ideas and suggestions so look forward to seeing the designs. the business logo has been supplied with this project and I want the card to be double sided

Contact info is
Colin Barrow - Managing Director / Horticulturist
Phone : 0481 526 704
Email: colinbarrow@verdantterraces.example.au

Target Market(s)

high class gardens residential and commercial

Industry/Entity Type

Gardener

Contact Information for Business Card

Contact info is
Phone : 0481 526 704

PLEASE MAKE CARD DOUBLE SIDED

Requirements
Must have
• organic simple classy modern feel
• must flow with the current logo that has been supplied with this project
• Double sided
• Must explain in a simple way that I deal with high end gardens and I'm a qualified horticulturist
Nice to have
• embossed debossed logo
Should not have
• shouldn't be to busy or cheap looking

```html
<!DOCTYPE html>
<html lang="en">
<head>
<meta charset="utf-8">
<title>Verdant Terraces – Business Card</title>
<link rel="stylesheet" href="https://fonts.googleapis.com/css2?family=Archivo:wght@400;600&display=swap">
<style>
  :root {
    --leaf: #4f8f43;
    --leaf-dark: #3f7a36;
    --leaf-pale: #e3eedf;
    --paper: #fbfbf8;
    --ink: #2b2b2b;
    --backdrop: #ece8e2;
  }
  * { box-sizing: border-box; margin: 0; padding: 0; }
  html, body {
    width: 1200px; height: 794px; overflow: hidden;
    background: var(--backdrop);
    font-family: "Archivo", Arial, sans-serif;
  }
  .sheet {
    width: 1200px; height: 794px;
    display: flex; align-items: center; justify-content: center; gap: 50px;
  }
  .card {
    width: 540px; height: 330px; position: relative; overflow: hidden;
    box-shadow: 0 6px 18px rgba(0,0,0,.12);
  }
  /* Front */
  .card--front {
    background: var(--leaf);
    display: flex; flex-direction: column; align-items: center; justify-content: center; gap: 16px;
  }
  .brand-dot {
    width: 54px; height: 54px; border-radius: 50%; background: var(--paper);
  }
  .brand-name {
    color: var(--paper); font-weight: 600; font-size: 30px;
    letter-spacing: .14em; text-transform: uppercase; white-space: nowrap;
  }
  /* Back */
  .card--back { background: var(--paper); }
  .back-brand {
    position: absolute; left: 34px; top: 52px;
    display: flex; align-items: center; gap: 10px;
  }
  .back-brand .brand-dot { width: 30px; height: 30px; background: var(--leaf); }
  .back-brand .brand-name { color: var(--leaf); font-size: 18px; letter-spacing: .1em; }
  .contact { position: absolute; left: 34px; top: 160px; width: 300px; }
  .contact__name { color: var(--leaf); font-weight: 600; font-size: 21px; }
  .contact__role { color: var(--ink); font-size: 15px; margin: 4px 0 16px; }
  .contact__line {
    display: flex; align-items: center; gap: 9px; white-space: nowrap;
    color: var(--ink); font-size: 13px; line-height: 1; margin-bottom: 9px;
  }
  .contact__line svg { width: 14px; height: 14px; flex: none; fill: var(--leaf); }
  .emblem-area {
    position: absolute; right: 30px; top: 30px; width: 160px; height: 256px;
    border-radius: 80px 80px 10px 10px;
    background: radial-gradient(circle at 50% 35%, var(--leaf-pale) 0%, #cfe2c9 70%, #c4dbbd 100%);
  }
  .card-band {
    position: absolute; left: 0; right: 0; bottom: 0; height: 14px; background: var(--leaf);
  }
</style>
</head>
<body>
<main class="sheet">
  <section class="card card--front" aria-label="Card front">
    <span class="brand-dot"></span>
    <span class="brand-name">Verdant Terraces</span>
  </section>

  <section class="card card--back" aria-label="Card back">
    <div class="back-brand">
      <span class="brand-dot"></span>
      <span class="brand-name">Verdant Terraces</span>
    </div>

    <div class="contact">
      <p class="contact__name">Colin Barrow</p>
      <p class="contact__role">Managing Director / Horticulturist</p>
      <p class="contact__line">
        <svg viewBox="0 0 16 16" aria-hidden="true"><path d="M3.6 1.5l2.3 2.6-1.4 1.6c.9 2 2.5 3.6 4.5 4.5l1.6-1.4 2.6 2.3-1.3 2.3C6.9 13.4 2.6 9.1 1.3 2.8z"/></svg>
        0481 526 704
      </p>
      <p class="contact__line">
        <svg viewBox="0 0 16 16" aria-hidden="true"><path d="M1 3h14v1.2L8 9 1 4.2zM1 5.6l7 4.8 7-4.8V13H1z"/></svg>
        colinbarrow@verdantterraces.example.au
      </p>
      <p class="contact__line">
        <svg viewBox="0 0 16 16" aria-hidden="true"><circle cx="8" cy="8" r="7"/><path d="M8 1v14M1 8h14" stroke="#fbfbf8" stroke-width="1.2"/></svg>
        verdantterraces.example.au
      </p>
    </div>

    <div class="emblem-area" role="img" aria-label="Large green tree emblem decoration"></div>
    <div class="card-band"></div>
  </section>
</main>
</body>
</html>
```